Tolbek cards

I want a simple business card that pops.
Logo on one side.
On side two i want.
"Are you thinking about a new building on your property, or renovating an existing structure? Contact".....
Owners Name: Dale Whitacre
Owners Phone number: 610-555-0187
Address:4076 Copper Ridge RD, Millbrook, OH 44108
Committed to Quality, Service, and Integrity

```html
<!DOCTYPE html>
<html lang="en">
<head>
<meta charset="utf-8">
<title>Tolbek Builders – Business Cards</title>
<link rel="stylesheet" href="https://fonts.googleapis.com/css2?family=Montserrat:wght@400;700&family=Cormorant+Garamond:wght@500&display=swap">
<style>
  :root {
    --bg-light: #e4e4e4;
    --bg-dark: #b9b9b9;
    --card-brown: #3e2a1b;
    --card-brown-deep: #2f2014;
    --band-taupe: #8f7964;
    --ink-light: #ffffff;
    --pattern-bronze: #6b4a2b;
  }
  * { margin: 0; padding: 0; box-sizing: border-box; }
  html, body { width: 1200px; height: 800px; overflow: hidden; }
  body {
    background: radial-gradient(circle at 60% 35%, var(--bg-light), var(--bg-dark));
    display: flex;
    align-items: center;
    justify-content: center;
    gap: 40px;
    font-family: "Montserrat", sans-serif;
  }
  .card {
    position: relative;
    width: 540px;
    height: 309px;
    background: var(--card-brown);
    color: var(--ink-light);
    box-shadow: 0 14px 30px rgba(0,0,0,0.28);
    overflow: hidden;
  }
  /* Info side */
  .headline-band {
    position: absolute;
    top: 24px;
    left: 30px;
    right: 0;
    height: 96px;
    background: var(--band-taupe);
    display: flex;
    align-items: center;
    padding: 0 24px;
  }
  .headline {
    font-weight: 700;
    font-size: 17px;
    line-height: 1.28;
    letter-spacing: 0.04em;
    text-transform: uppercase;
    text-align: center;
    width: 100%;
  }
  .rule {
    position: absolute;
    left: 50px;
    right: 50px;
    height: 1px;
    background: var(--ink-light);
    opacity: 0.85;
  }
  .rule--top { top: 140px; }
  .rule--bottom { bottom: 20px; }
  .contact {
    position: absolute;
    top: 150px;
    left: 0;
    right: 0;
    text-align: center;
  }
  .contact-label {
    display: flex;
    align-items: center;
    justify-content: center;
    gap: 8px;
    font-size: 11px;
    letter-spacing: 0.08em;
  }
  .contact-label::before,
  .contact-label::after {
    content: "";
    width: 60px;
    height: 1px;
    background: var(--ink-light);
  }
  .owner-name {
    margin-top: 6px;
    font-weight: 700;
    font-size: 17px;
    letter-spacing: 0.06em;
    text-transform: uppercase;
  }
  .owner-phone {
    font-size: 12px;
    letter-spacing: 0.1em;
    margin-top: 2px;
  }
  .short-rule {
    width: 50px;
    height: 1px;
    background: var(--ink-light);
    margin: 7px auto 8px;
  }
  .address {
    font-size: 12px;
    letter-spacing: 0.06em;
    white-space: nowrap;
  }
  .tagline {
    font-family: "Cormorant Garamond", serif;
    font-weight: 500;
    font-size: 19px;
    margin-top: 8px;
    white-space: nowrap;
  }
  /* Brand side */
  .brand-pattern {
    position: absolute;
    inset: 0;
    background:
      radial-gradient(ellipse at 85% 10%, rgba(140,98,56,0.55), transparent 60%),
      linear-gradient(160deg, var(--pattern-bronze), var(--card-brown) 55%, var(--card-brown-deep));
  }
  .brand-lockup {
    position: absolute;
    left: 50%;
    top: 58%;
    transform: translate(-50%, -50%);
    display: flex;
    align-items: center;
    gap: 12px;
    white-space: nowrap;
  }
  .brand-mark {
    flex: none;
    width: 24px;
    height: 24px;
    background: var(--ink-light);
  }
  .brand-name {
    font-weight: 700;
    font-size: 26px;
    letter-spacing: 0.04em;
    line-height: 1;
    text-transform: uppercase;
  }
</style>
</head>
<body>
  <section class="card card--info">
    <div class="headline-band">
      <p class="headline">Are you thinking about a new building on your property, or renovating an existing structure?</p>
    </div>
    <div class="rule rule--top"></div>
    <div class="contact">
      <p class="contact-label">Contact</p>
      <p class="owner-name">Dale Whitacre</p>
      <p class="owner-phone">610-555-0187</p>
      <div class="short-rule"></div>
      <p class="address">4076 Copper Ridge RD, Millbrook, OH 44108</p>
      <p class="tagline">Committed to Quality, Service and Integrity</p>
    </div>
    <div class="rule rule--bottom"></div>
  </section>

  <section class="card card--brand">
    <div class="brand-pattern" role="img" aria-label="Tonal bronze repeating brand pattern across the card"></div>
    <div class="brand-lockup">
      <span class="brand-mark"></span>
      <span class="brand-name">Tolbek Builders LLC</span>
    </div>
  </section>
</body>
</html>
```